Stationery Design Project

We need a stationery design for our Norwegian trucking company. We have existed for about 15 years and our 12 drivers uses relatively new vehicles to transport goods around in northern Norway. Long distance routes with fresh fish og food transport is our main operations.

We have already made alogo that's printed on our trucks. The logo and a picture of our trucks is attached. I think the logo i crappy, but since its already in use, changing it is not an option in this round. Still using a better colour scheme in the overall stationery and more interesting fonts is possible (altso in the logo).

Company details:
Name: Kjelvraket AS
Organisation nr 873 615 309
Post adress: 8642 Raudvik

I like minimalism and simplicity. I am avalibly for questions in normal GMT working hours either here or on mail: ivar@fjordlast.no

Reason: Hi. Im extending the deadline because I needed some time to find a vector file of our logo. Sorry for the inconvenience

Hi, and thanks for all your interest in the project. Some updates:

-          I have decided to commit to using one of the designs. Some designer will get the payment.

-          I have extended the deadline with 24 hours since I needed some time to find our firms vector logo (a slow Swedish man was holding me up)

-          We will not choose a design before the deadline. No need to rush.

-          We have received a lot of great design and think there is a need to specified the product we want to make:

o   Business Card for all our employers. I just need the design and will duplicate with the correct numbers and name myself. The information on should be: Logo, employer’s name, Phone number, email, website, Postal number and address. Use this as a template: logo, Leif Brattvoll, 47382066, Leif@fjordlast.no,, fjordlast.no, 8642 Raudvik. The order and placement of the information is your creative decision.

o   Stickers to put on the goods we travel. On the sticker the should be the following information: Logo, phone number, Tekst and link: Fraktæ av Kjelvraket. Ke du syns? Fjordlast.no/tilbakemelding (this means: Handled by Kjelvraket. What do you think Fjordlast.no/feedback -à the link will be a feedback form). The placement the information and size is your creative decision with some stings: we have been thinking of using Drukko for printing and see that a size about 6x6 cm, 8x5 or something like that. (with 3000 copies our budget is 200 punds). Any suggestions of other suppliers are welcome. Drukko price calculator http://www.drukkolabelhouse.co.uk/digital-litho-printing/printing-labels-tags/stickers/

o   Letterhead with logo, address, phone number and organizational number.

o   Envelopes with logo,address, phone number and organizational number.

Have a nice day.

 

 

• Using the blue colour in the logo and using a similar graphic approch.

```html
<!DOCTYPE html>
<html lang="no">
<head>
<meta charset="utf-8">
<title>Kjelvraket AS – visittkort</title>
<link rel="stylesheet" href="https://fonts.googleapis.com/css2?family=Open+Sans:wght@400;700&family=Tinos:wght@700&display=swap">
<style>
  :root {
    --page: #d9dbde;
    --white: #ffffff;
    --sky: #0b72b9;
    --ocean: #0a52a3;
    --deep: #173f92;
    --ink: #222a33;
    --card-w: 519px;
    --card-h: 296px;
  }
  * { box-sizing: border-box; margin: 0; padding: 0; }
  html, body { width: 1200px; height: 732px; overflow: hidden; }
  body {
    background: var(--page);
    position: relative;
    font-family: "Open Sans", Arial, sans-serif;
  }
  .card {
    position: absolute;
    width: var(--card-w);
    height: var(--card-h);
    overflow: hidden;
    box-shadow: 0 1px 3px rgba(0,0,0,.25);
  }
  .card--front { left: 61px; top: 45px; background: var(--white); }
  .card--back-white { left: 617px; top: 43px; background: var(--white); border: 1px solid #c9ccd1; }
  .card--back-sky { left: 61px; top: 386px; background: var(--sky); }
  .card--back-ocean { left: 617px; top: 382px; background: var(--ocean); }

  .brand-name {
    position: absolute;
    font-family: "Open Sans", Arial, sans-serif;
    font-weight: 700;
    letter-spacing: 0.5px;
    white-space: nowrap;
  }
  .card--front .brand-name { left: 0; width: 420px; top: 62px; text-align: center; font-size: 34px; color: var(--ocean); }
  .card--back-white .brand-name,
  .card--back-sky .brand-name,
  .card--back-ocean .brand-name { left: 0; right: 0; top: 118px; text-align: center; font-size: 40px; }
  .card--back-white .brand-name { color: var(--ocean); }
  .card--back-sky .brand-name, .card--back-ocean .brand-name { color: var(--white); }

  .web-line {
    position: absolute;
    left: 0; right: 0;
    top: 248px;
    text-align: center;
    font-size: 16px;
    letter-spacing: 3.5px;
  }
  .card--back-white .web-line { color: var(--ink); }
  .card--back-sky .web-line, .card--back-ocean .web-line { color: var(--white); }

  .footer-rule {
    position: absolute;
    left: 0; right: 0;
    top: 262px;
    height: 2px;
    background: var(--deep);
  }
  .footer-band {
    position: absolute;
    left: 0; right: 0; bottom: 0;
    height: 30px;
    background: var(--sky);
  }

  .contact-list {
    position: absolute;
    left: 68px; top: 147px;
    list-style: none;
    font-size: 13.5px;
    color: var(--ink);
    line-height: 21px;
  }
  .contact-list li { display: flex; align-items: center; gap: 4px; }
  .contact-list .gap { margin-top: 13px; }
  .contact-list .label { color: var(--sky); }
  .icon { width: 11px; height: 11px; fill: var(--sky); flex: none; }

  .person-name {
    position: absolute;
    right: 32px; top: 269px;
    font-family: "Tinos", "Times New Roman", serif;
    font-weight: 700;
    font-size: 17.5px;
    line-height: 22px;
    color: var(--white);
  }
</style>
</head>
<body>

<section class="card card--front" aria-label="Visittkort forside">
  <div class="footer-rule"></div>
  <div class="footer-band"></div>

  <div class="brand-name">Kjelvraket</div>

  <ul class="contact-list">
    <li>
      <svg class="icon" viewBox="0 0 12 12" aria-hidden="true"><path d="M2.5 1 L4.5 3.2 L3.6 4.6 C4.3 6 5.9 7.6 7.4 8.4 L8.8 7.5 L11 9.5 L9.8 11 C5.5 10.6 1.4 6.5 1 2.2 Z"/></svg>
      47382066
    </li>
    <li><span class="label">Org nr</span>&nbsp;873 615 309</li>
    <li>
      <svg class="icon" viewBox="0 0 12 12" aria-hidden="true"><path d="M1 3 H11 V10 H1 Z M1.6 3.6 L6 7 L10.4 3.6" stroke="var(--white)" stroke-width=".9"/></svg>
      Leif@fjordlast.no
    </li>
    <li>
      <svg class="icon" viewBox="0 0 12 12" aria-hidden="true"><circle cx="6" cy="6" r="5"/><path d="M1 6 H11 M6 1 C3.5 4 3.5 8 6 11 M6 1 C8.5 4 8.5 8 6 11" stroke="var(--white)" stroke-width=".8" fill="none"/></svg>
      www.fjordlast.no
    </li>
    <li class="gap">
      <svg class="icon" viewBox="0 0 12 12" aria-hidden="true"><path d="M1 5 L6 2 L11 5 V11 H1 Z"/></svg>
      8642 Raudvik
    </li>
  </ul>

  <div class="person-name">Leif Brattvoll</div>
</section>

<section class="card card--back-white" aria-label="Visittkort bakside hvit">
  <div class="brand-name">Kjelvraket</div>
  <div class="web-line">www.fjordlast.no</div>
</section>

<section class="card card--back-sky" aria-label="Visittkort bakside lyseblå">
  <div class="brand-name">Kjelvraket</div>
  <div class="web-line">www.fjordlast.no</div>
</section>

<section class="card card--back-ocean" aria-label="Visittkort bakside mørkeblå">
  <div class="brand-name">Kjelvraket</div>
  <div class="web-line">www.fjordlast.no</div>
</section>

</body>
</html>
```